Need Website Design for Non-Profit Veteran Site

I am looking for a very talented creative website designer for a modern feel. I'll give a little bit of guidance around what I am looking for and then your creative juices should kick in and design away. I have already purchased the domain but will need hosting (at least temporarily) and the creative design work done.The website domain is militarydocs.orgI am looking to attract current and veteran military providers (doctors, nurse practitioners, physician assistants, etc) to join and signup for membership. They would pay a yearly fee to join. Would need membership categories $135 for Provider, $55 Student, $100 for Retired, and Organization (Organization would be broken down into Less than 100 ($200), 100-249 ($250), 250-499 ($300), 500-999 ($400), 1,000-2,999 ($500), and 3,000 ($700). Would need Benefit built out and would need to accept money through CoinVane and other means. Since it's a new organization just starting, would also need a Donate button to get people to donate if they want any amount they would like. The second part of the website is that once they join, they will have acess to a list of all other providers who have registered within the website (not exportable) so they can connect with one another. If they want to see contact information this will be included in their fee as a benefit to socialize with one another. As part of the website, there will be another Veteran's portal so veterans who would like to connect with a provider around a particular speciality can reach out and request help from the doctor writing a nexus letter or letter to support the veteran who is filing a claim with the BQ. Veterans would pay a yearly sign-up fee of $30.00 and would need their membership benefits displayed. They would have access to a list of veterans in their region by state and distance, and can reach out to doctors to get their help. If a doctor and veteran agree, sharable inforamtion of medical hipaa documents can be exchanged via the website. The physician and veteran can negotiate a fee through the website only and share their details. This is a separate fee for this type of process between the provider and veteran. We will collect a $250 fee for admin on each of these and each project the veteran does with the provider will cost $450 (so essentially the doctor gets paid $450 and i get $250.00. This model could be changed over time as we start to test this out). A good example of 50% of what I'm looking for is something like the following website: https://www.lpkt.org/ It has some of the features but not all and my site should be more modernized to attract the veteran and military providers.

Target Market(s)

Current and retired military providers and veterans

Industry/Entity Type

Non Profit

Number of Pages Required

1 page

Requirements
Must have
• Military Design
• Modern Feel (Example templates for feel -https://quillmoth.com/free-photoshop-psd-web-design-template/)
• Donation box
• Stuff mentioned in the description)
Nice to have
• Open to feedback
Should not have
• Open to feedback

```html
<!DOCTYPE html>
<html lang="en">
<head>
<meta charset="utf-8">
<title>Harborwell — Veteran Provider Network</title>
<link href="https://fonts.googleapis.com/css2?family=Lora:wght@400;700&family=Open+Sans:wght@400;600;700&display=swap" rel="stylesheet">
<style>
  :root{
    --olive-dark:#4f4d34;
    --olive:#6d6b4a;
    --olive-light:#8a8762;
    --header:#2c2b22;
    --red:#a63a2b;
    --red-dark:#8f2f22;
    --ink:#3a3a34;
    --muted:#7a7a72;
    --page:#ffffff;
    --footer:#efeee9;
    --bar:#3a3929;
    --rule:#dddcd5;
  }
  *{margin:0;padding:0;box-sizing:border-box}
  html,body{width:696px;height:1200px;overflow:hidden}
  body{position:relative;font-family:"Open Sans",Arial,sans-serif;color:var(--ink);
    background:linear-gradient(135deg,var(--olive-dark) 0%,var(--olive) 35%,var(--olive-light) 55%,var(--olive) 75%,var(--olive-dark) 100%)}
  .abs{position:absolute}
  .page{position:absolute;left:46px;top:0;width:604px;height:1188px;background:var(--page)}

  /* header */
  .site-header{position:absolute;left:0;top:0;width:604px;height:46px;background:var(--header);display:flex;align-items:center;padding:0 10px}
  .brand{font-family:"Open Sans",sans-serif;font-weight:700;font-size:15px;color:#fff;letter-spacing:.5px;text-transform:uppercase}
  .nav{display:flex;gap:12px;margin-left:auto;align-items:center}
  .nav a{color:#e8e6dc;font-size:6.5px;font-weight:600;text-decoration:none;letter-spacing:.3px}
  .nav .btn-signup{background:var(--red);color:#fff;padding:5px 7px}
  .nav .btn-join{background:#55533c;color:#fff;padding:5px 7px}

  /* hero */
  .hero{position:absolute;left:0;top:46px;width:604px;height:318px;
    background:linear-gradient(90deg,#d9d4cb 0%,#c9c2b4 30%,#bdb7a6 55%,#8a8566 75%,#6b6a4c 100%)}
  .hero-card{position:absolute;left:186px;top:140px;width:232px;height:159px;background:rgba(92,80,62,.72);text-align:center;color:#fff;padding:18px 20px}
  .hero-card h1{font-family:"Lora",serif;font-weight:400;font-size:22px;margin-bottom:10px}
  .hero-card p{font-size:6.5px;line-height:1.6;color:#f1eee6}
  .btn-red{display:inline-block;background:var(--red);color:#fff;font-size:6.5px;font-weight:600;padding:6px 11px;text-transform:uppercase}
  .hero-card .btn-red{margin-top:14px}

  /* intro */
  .section-title{font-family:"Lora",serif;font-weight:400;font-size:14px;color:#4a4838}
  .body-text{font-size:6.5px;line-height:1.7;color:var(--muted)}
  .welcome{left:12px;top:380px;width:340px}
  .welcome .section-title{margin-bottom:12px}
  .welcome .body-text{margin-bottom:10px}
  .welcome .btn-red{margin-top:4px;text-transform:none;font-size:7px}
  .news{left:368px;top:380px;width:222px}
  .news .section-title{margin-bottom:16px}
  .news-item{display:flex;gap:10px;margin-bottom:18px}
  .date{flex:0 0 34px;height:34px;border:1px solid var(--red);border-radius:50%;text-align:center;color:var(--red);font-family:"Lora",serif;padding-top:4px}
  .date b{display:block;font-size:12px;font-weight:400;line-height:1.1}
  .date span{font-size:6px}
  .news-item h3{font-family:"Lora",serif;font-weight:400;font-size:8.5px;color:var(--red);margin-bottom:4px}

  /* three columns */
  .feature{top:612px;width:182px}
  .feature .section-title{margin-bottom:8px}
  .feature .photo{width:182px;height:123px;margin-bottom:10px}
  .btn-outline{display:inline-block;border:1px solid #bdbcb3;color:var(--muted);font-size:6px;padding:5px 8px;margin-top:10px;text-transform:uppercase}

  /* callout */
  .callout{position:absolute;left:0;top:877px;width:604px;height:137px;background:var(--red);text-align:center;color:#fff;padding-top:28px}
  .callout h2{font-family:"Lora",serif;font-weight:400;font-size:14px;letter-spacing:.3px;text-transform:uppercase}
  .callout p{font-family:"Lora",serif;font-size:8px;margin-top:6px;color:#f3ddd8}
  .btn-light{display:inline-block;border:1px solid #e9c4bc;color:#fff;font-size:6.5px;padding:7px 12px;margin-top:14px;text-transform:uppercase}

  /* footer */
  .site-footer{position:absolute;left:0;top:1028px;width:604px;height:134px;background:var(--footer)}
  .footer-col{position:absolute;top:14px}
  .footer-col h4{font-size:7px;font-weight:600;color:#4a4838;margin-bottom:8px;text-transform:uppercase}
  .footer-col li{list-style:none;font-size:6px;color:var(--muted);line-height:1.9;display:flex;align-items:center;gap:5px}
  .footer-col li svg{flex:0 0 auto}
  .input{width:96px;height:14px;border:1px solid #cfcec6;background:#fff;font-size:5.5px;color:#9a998f;padding:3px 4px;margin:7px 0 6px}
  .footer-col .btn-red{font-size:5.5px;padding:4px 7px}
  .socials{display:flex;gap:5px;margin-top:10px}
  .socials span{width:13px;height:13px;border:1px solid #b8b7ae;border-radius:50%}
  .copyright{position:absolute;left:0;top:1162px;width:604px;height:26px;background:var(--bar);color:#cfcdbf;font-size:6px;text-align:center;line-height:26px}
</style>
</head>
<body>
  <div class="page">
    <header class="site-header">
      <div class="brand">Harborwell</div>
      <nav class="nav">
        <a>HOME</a><a>ABOUT US</a><a>SERVICES</a><a>DONATE</a><a>NEWS</a><a>CONTACT US</a>
        <a class="btn-signup">MEMBERSHIP SIGNUP</a><a class="btn-join">JOIN HERE</a>
      </nav>
    </header>

    <section class="hero" role="img" aria-label="Photo of a doctor in a white coat speaking with a soldier in camouflage uniform">
      <div class="hero-card">
        <h1>Harborwell</h1>
        <p>Sed ut perspiciatis unde omnis iste natus error sit voluptatem accusantium doloremque laudantium, totam rem aperiam eaque ipsa quae ab illo inventore veritatis.</p>
        <span class="btn-red">Donate Now</span>
      </div>
    </section>

    <section class="abs welcome">
      <h2 class="section-title">Welcome To Our Company</h2>
      <p class="body-text">Sed ut perspiciatis unde omnis iste natus error sit voluptatem accusantium doloremque laudantium, totam rem aperiam, eaque ipsa quae ab illo inventore veritatis et quasi architecto beatae vitae dicta sunt explicabo nemo enim ipsam.</p>
      <p class="body-text">Sed ut perspiciatis unde omnis iste natus error sit voluptatem accusantium doloremque laudantium, totam rem aperiam eaque ipsa quae ab illo inventore veritatis et quasi architecto.</p>
      <p class="body-text">Nemo enim ipsam voluptatem quia voluptas sit aspernatur aut odit aut fugit, sed quia consequuntur magni dolores eos qui ratione sequi nesciunt.</p>
      <span class="btn-red">Read More</span>
    </section>

    <section class="abs news">
      <h2 class="section-title">Latest News</h2>
      <article class="news-item">
        <div class="date"><b>03</b><span>Feb</span></div>
        <div><h3>Sed ut perspiciatis unde omnis</h3>
          <p class="body-text">Iste natus error sit voluptatem accusantium doloremque laudantium totam rem aperiam.</p></div>
      </article>
      <article class="news-item">
        <div class="date"><b>03</b><span>Feb</span></div>
        <div><h3>Sed ut perspiciatis unde omnis</h3>
          <p class="body-text">Iste natus error sit voluptatem accusantium doloremque laudantium totam rem aperiam.</p></div>
      </article>
    </section>

    <section class="abs feature" style="left:5px">
      <h2 class="section-title">About Us</h2>
      <div class="photo" role="img" aria-label="Photo of a team meeting around a desk" style="background:linear-gradient(135deg,#b9b6ae,#8e8b82)"></div>
      <p class="body-text">Sed ut perspiciatis unde omnis iste natus error sit voluptatem accusantium doloremque laudantium totam rem.</p>
      <span class="btn-outline">Read More</span>
    </section>
    <section class="abs feature" style="left:205px">
      <h2 class="section-title">Our Services</h2>
      <div class="photo" role="img" aria-label="Photo of a doctor examining a patient with a stethoscope" style="background:linear-gradient(135deg,#d8d2c8,#a89e8e)"></div>
      <p class="body-text">Sed ut perspiciatis unde omnis iste natus error sit voluptatem accusantium doloremque laudantium totam rem.</p>
      <span class="btn-outline">Read More</span>
    </section>
    <section class="abs feature" style="left:406px">
      <h2 class="section-title">Donation</h2>
      <div class="photo" role="img" aria-label="Photo of a glass jar of coins" style="background:linear-gradient(135deg,#e3d7bd,#b8965e)"></div>
      <p class="body-text">Sed ut perspiciatis unde omnis iste natus error sit voluptatem accusantium doloremque laudantium totam rem.</p>
      <span class="btn-outline">Read More</span>
    </section>

    <section class="callout">
      <h2>Sed ut perspiciatis unde omnis iste natus voluptatem</h2>
      <p>error sit voluptatem accusantium doloremque laudantium</p>
      <span class="btn-light">Click Here For More Info</span>
    </section>

    <footer class="site-footer">
      <div class="footer-col" style="left:34px">
        <h4>Quick Links</h4>
        <ul>
          <li>› Home</li><li>› About Us</li><li>› Services</li><li>› Donate</li><li>› News</li><li>› Contact Us</li>
        </ul>
      </div>
      <div class="footer-col" style="left:144px">
        <h4>Contact Us</h4>
        <ul>
          <li><svg width="7" height="7" viewBox="0 0 10 10"><path d="M2 1l2 2-1 1.5a6 6 0 0 0 2.5 2.5L7 6l2 2-1.5 1.5C4.5 9 1 5.5.5 2.5z" fill="#8a8980"/></svg>(555) 014-2231</li>
          <li><svg width="7" height="7" viewBox="0 0 10 10"><path d="M2 1l2 2-1 1.5a6 6 0 0 0 2.5 2.5L7 6l2 2-1.5 1.5C4.5 9 1 5.5.5 2.5z" fill="#8a8980"/></svg>(555) 014-2298</li>
          <li><svg width="7" height="7" viewBox="0 0 10 10"><rect x="1" y="2" width="8" height="6" fill="none" stroke="#8a8980"/><path d="M1 2l4 3 4-3" fill="none" stroke="#8a8980"/></svg>info@harborwellnet.org</li>
          <li><svg width="7" height="7" viewBox="0 0 10 10"><path d="M5 9.5S1.5 6 1.5 4a3.5 3.5 0 0 1 7 0c0 2-3.5 5.5-3.5 5.5z" fill="#8a8980"/><circle cx="5" cy="4" r="1.2" fill="#efeee9"/></svg>75 Larchmont Avenue, Fairhaven</li>
        </ul>
      </div>
      <div class="footer-col" style="left:300px">
        <h4>Newsletter</h4>
        <p class="body-text" style="width:110px">Sign up to receive our latest updates and news by email.</p>
        <div class="input">Email Address</div>
        <span class="btn-red">Subscribe</span>
      </div>
      <div class="footer-col" style="left:460px">
        <h4>Follow Us</h4>
        <p class="body-text" style="width:110px">Stay connected with our members and share our mission with friends.</p>
        <div class="socials"><span></span><span></span><span></span><span></span></div>
      </div>
    </footer>
    <div class="copyright">© Copyright 2016 Harborwell. All Rights Reserved</div>
  </div>
</body>
</html>
```